Spy/Espionage/Counterintelligence Membership Community Needs a PowerPoint Template

We need a powerpoint template for one of our business verticals focused on spies, espionage, and counterintelligence. The name of it is "Brass Lantern Guild" and the logo is attached. Brass Lantern Guild is a community that connects people with experts in espionage and counterintelligence through an online social network, as well as in-person events. We would like to see designs that incorporate the red and black of the logo. The design should communicate mystery/suspense and peak curiosity.

Target Market(s)

Late 20s to baby boomers, male

Industry/Entity Type

Social Club

Font styles to use
Sans Serif

Colors
ec1f27
000000
ffffff

Requirements
Must have
• A user-friendly ppt template file. Incorporate basic fonts that don't have to be installed on every computer for presentations. A cover slide and a basic inside slide. A white background. I will also need graphic source files.
Nice to have
• Plenty of space for slide title and body content. Logo on every slide.
Should not have
• Inconsistency with fonts. Misalignment of images.

```html
<!DOCTYPE html>
<html lang="en">
<head>
<meta charset="utf-8">
<title>Brass Lantern Guild – Presentation Template</title>
<link href="https://fonts.googleapis.com/css2?family=Questrial&family=Open+Sans:wght@400;600;700&display=swap" rel="stylesheet">
<style>
:root{
  --red:#d0141b;
  --red-bright:#ec1f27;
  --red-dark:#a01a20;
  --black:#1a1a1a;
  --ink:#222;
  --grey-text:#8a8a8a;
  --grey-mid:#666;
  --grey-light:#d9d9d9;
  --pink:#f6d9da;
  --stage:#6b6b6b;
  --white:#fff;
}
*{box-sizing:border-box;margin:0;padding:0}
html,body{width:1195px;height:1200px;overflow:hidden}
body{background:var(--stage);position:relative;font-family:"Open Sans",sans-serif;color:var(--ink)}
.slide{position:absolute;width:371px;height:278px;background:var(--white);overflow:hidden}
.c1{left:28px}.c2{left:415px}.c3{left:803px}
.r1{top:27px}.r2{top:324px}.r3{top:614px}.r4{top:900px}
.header{position:absolute;left:0;top:0;width:100%;height:24px;background:var(--red);display:flex;align-items:center;justify-content:space-between;padding:0 6px}
.header h2{font-family:"Questrial",sans-serif;font-weight:400;font-size:14px;color:var(--white)}
.brand{display:flex;align-items:center;gap:3px;font-family:"Questrial",sans-serif;font-size:9.5px;color:var(--white)}
.brand .dot{width:11px;height:11px;border-radius:50%;background:var(--black)}
.footer{position:absolute;left:0;bottom:0;width:100%;height:13px;background:var(--black);display:flex;align-items:center;justify-content:space-between;padding:0 4px;font-size:6px;color:var(--white)}
.page{width:10px;height:10px;border-radius:50%;background:var(--red-bright);border:1px solid var(--white);font-size:6px;line-height:8px;text-align:center}
.copy{font-size:6.2px;line-height:10.5px;color:var(--grey-text)}
.red-head{font-size:7.5px;font-weight:600;color:var(--red);margin-bottom:2px}
.abs{position:absolute}
.lead{font-size:6.8px;font-weight:700;color:var(--black)}

/* cover */
.cover-mark{position:absolute;left:238px;top:77px;width:56px;height:56px;border-radius:50%;background:var(--red-bright);border:3px solid var(--black)}
.wordmark{font-family:"Questrial",sans-serif;font-size:21px;color:var(--black)}
.cover-title{position:absolute;right:23px;top:184px;font-family:"Questrial",sans-serif;font-size:19px;color:var(--red-bright)}
.cover-sub{position:absolute;right:23px;top:209px;text-align:right;font-size:7.5px;line-height:12px;color:var(--ink)}
.band-bottom{position:absolute;left:0;bottom:0;width:100%;height:12px;background:var(--black)}

/* bullets */
.bullets{position:absolute;left:16px;top:49px;list-style:none}
.bullets li{display:flex;align-items:center;gap:7px;height:20.5px;font-size:7.4px;color:var(--grey-mid)}
.bullets li::before{content:"";width:11px;height:11px;border-radius:50%;background:var(--red-bright);border:1.5px solid var(--black)}

/* timeline */
.year{position:absolute;top:96px;width:30px;height:30px;border-radius:50%;border:2px solid var(--white);box-shadow:0 0 0 1px #bbb;color:var(--white);font-size:9px;font-weight:700;display:flex;align-items:center;justify-content:center}
.card{position:absolute;top:130px;width:102px;height:122px;border:1px solid #e2b8ba}
.card.grey{border-color:#bbb}
.card h3{height:18px;color:var(--white);font-size:6.8px;font-weight:700;text-align:center;line-height:18px}
.card p{font-size:5.5px;line-height:9.3px;color:#555;padding:4px 11px}

/* table */
.data-table{position:absolute;left:23px;top:93px;width:310px;border-collapse:collapse;font-size:6px}
.data-table th{background:var(--red-bright);color:var(--white);font-size:7.2px;font-weight:700;height:18px;text-align:center}
.data-table td{height:20px;text-align:center;color:#333}
.data-table tr:nth-child(odd) td{background:#dcdcdc}
.data-table tr:nth-child(even) td{background:var(--pink)}

/* icon rows */
.icon-row{position:absolute;left:0;width:340px;height:40px}
.chev{position:absolute;left:0;top:0;width:71px;height:40px;background:#8c8c8c;clip-path:polygon(0 0,86% 0,100% 50%,86% 100%,0 100%)}
.icon-row .chev svg{position:absolute;left:25px;top:9px}
.icon-text{position:absolute;left:79px;top:2px;width:260px}
.icon-text h4{font-size:7px;font-weight:600;color:var(--red)}
.icon-text h4 span{color:var(--grey-mid)}
.icon-text p{font-size:4.9px;line-height:7px;color:#999}

/* closing */
.closing{background:var(--red-bright)}
.closing-title{position:absolute;left:16px;top:126px;font-family:"Questrial",sans-serif;font-size:17px;color:var(--white)}
.contact-box{position:absolute;left:167px;top:74px;width:204px;height:139px;background:var(--white);text-align:center}
.contact-box .mark{width:40px;height:40px;border-radius:50%;background:var(--red-bright);border:2px solid var(--black);margin:17px auto 4px}
.contact-box p{font-size:7.8px;line-height:12.5px;color:var(--ink)}
</style>
</head>
<body>

<!-- Cover -->
<section class="slide c1 r1">
  <div class="cover-mark"></div>
  <div class="abs wordmark" style="left:182px;top:139px;">Brass Lantern Guild</div>
  <div class="cover-title">Project Title Here</div>
  <div class="cover-sub">Subtext here Subtext here Subtext here<br>Subtext here Subtext here Subtext here<br>Subtext here Subtext here</div>
  <div class="band-bottom"></div>
</section>

<!-- Blank inside -->
<section class="slide c2 r1">
  <header class="header"><h2>Project Title Here</h2><div class="brand"><span class="dot"></span>Brass Lantern Guild</div></header>
  <footer class="footer"><span>Copyright text here</span><span class="page">1</span></footer>
</section>

<!-- Bullets -->
<section class="slide c3 r1">
  <header class="header"><h2>Project Title Here</h2><div class="brand"><span class="dot"></span>Brass Lantern Guild</div></header>
  <ul class="bullets">
    <li>Lorem ipsum dolor sit Lorem Lorem ipsum dolor sit Lorem</li>
    <li>Lorem ipsum dolor sit Lorem Lorem ipsum dolor sit Lorem</li>
    <li>Lorem ipsum dolor sitLorem ipsum dolor sit Lorem Lorem</li>
    <li>Lpsum dolor sit Lorem Lorem Lorem ipsum dolor sit Lorem</li>
    <li>Lorem ipsum dolor sit Lorem Lorem ipsum dolor sit Lorem</li>
    <li>Lorem ipsum dolor sit Lorem Lorem ipsum dolor sit Lorem</li>
    <li>Lorem ipsum dolor sit Lorem Lorem ipsum dolor sit Lorem</li>
    <li>Lorem ipsum dolor sit Lorem Lorem ipsum dolor sit Lorem</li>
    <li>Lorem ipsum dolor sit Lorem Lorem ipsum dolor sit Lorem</li>
  </ul>
  <footer class="footer"><span>Copyright text here</span><span class="page">1</span></footer>
</section>

<!-- Two columns -->
<section class="slide c1 r2">
  <header class="header"><h2>Project Title Here</h2><div class="brand"><span class="dot"></span>Brass Lantern Guild</div></header>
  <div class="abs" style="left:13px;top:51px;width:170px;">
    <div class="red-head">Lorem ipsum dolor sit Lorem</div>
    <p class="copy">Lorem ipsum dolor sit Lorem ipsum dolor sit Lorem ipsum dolor sit Lorem ipsum dolor sit Lorem ipsum dolor sit Lorem ipsum dolor sit Lorem ipsum dolor sit Lorem ipsum dolor sit Lorem ipsum dolor sit Lorem ipsum dolor sit Lorem ipsum dolor sit Lorem ipsum dolor sit Lorem ipsum dolor sit Lorem ipsum dolor sit Lorem ipsum dolor sit Lorem ipsum dolor sit</p>
    <p class="copy" style="margin-top:14px;">Lorem ipsum dolor sit Lorem ipsum dolor sit Lorem ipsum dolor sit Lorem ipsum dolor sit Lorem ipsum dolor sit Lorem ipsum dolor sit Lorem ipsum dolor sit Lorem ipsum dolor sit Lorem ipsum dolor sit Lorem ipsum dolor sit Lorem ipsum dolor sit Lorem ipsum dolor sit Lorem ipsum dolor sit Lorem ipsum dolor sit Lorem ipsum dolor sit Lorem ipsum dolor sit</p>
  </div>
  <div class="abs" style="left:199px;top:51px;width:170px;">
    <div class="red-head">Lorem ipsum dolor sit Lorem</div>
    <p class="copy">Lorem ipsum dolor sit Lorem ipsum dolor sit Lorem ipsum dolor sit Lorem ipsum dolor sit Lorem ipsum dolor sit Lorem ipsum dolor sit Lorem ipsum dolor sit Lorem ipsum dolor sit Lorem ipsum dolor sit Lorem ipsum dolor sit Lorem ipsum dolor sit Lorem ipsum dolor sit Lorem ipsum dolor sit Lorem ipsum dolor sit Lorem ipsum dolor sit Lorem ipsum dolor sit</p>
    <p class="copy" style="margin-top:14px;">Lorem ipsum dolor sit Lorem ipsum dolor sit Lorem ipsum dolor sit Lorem ipsum dolor sit Lorem ipsum dolor sit Lorem ipsum dolor sit Lorem ipsum dolor sit Lorem ipsum dolor sit Lorem ipsum dolor sit Lorem ipsum dolor sit Lorem ipsum dolor sit Lorem ipsum dolor sit Lorem ipsum dolor sit Lorem ipsum dolor sit Lorem ipsum dolor sit Lorem ipsum dolor sit</p>
  </div>
  <footer class="footer"><span>Copyright text here</span><span class="page">1</span></footer>
</section>

<!-- Timeline -->
<section class="slide c2 r2">
  <header class="header"><h2>Project Title Here</h2><div class="brand"><span class="dot"></span>Brass Lantern Guild</div></header>
  <div class="abs" style="left:16px;top:39px;width:340px;">
    <p class="lead">Lorem ipsum dolor sit Lorem ipsum dolor sit &nbsp;Lorem ipsum dolor sit</p>
    <p style="font-size:5.6px;line-height:9.2px;color:#555;margin-top:5px;">Lorem ipsum dolor sit Lorem ipsum dolor sit Lorem ipsum dolor sit Lorem ipsum dolor sit Lorem ipsum dolor sit Lorem ipsum dolor sit Lorem ipsum dolor sit Lorem ipsum dolor sit Lorem ipsum dolor sit Lorem ipsum dolor sit Lorem ipsum dolor sit Lorem ipsum dolor sit Lorem ipsum dolor sit Lorem ipsum dolor sit Lorem ipsum dolor sit</p>
  </div>
  <div class="abs" style="left:68px;top:111px;width:235px;height:1px;background:#bbb;"></div>
  <div class="year" style="left:53px;background:var(--red-bright);">1995</div>
  <div class="year" style="left:170px;background:var(--red);">2005</div>
  <div class="year" style="left:288px;background:#555;">2015</div>
  <div class="card" style="left:17px;"><h3 style="background:var(--red-bright);">TITLE HERE</h3><p>Lorem ipsum dolor sit Lorem ipsum dolor sit Lorem ipsum dolor sit Lorem ipsum dolor sit Lorem ipsum dolor sit Lorem ipsum dolor sit Lorem ipsum dolor sit Lorem ipsum dolor sit Lorem ipsum dolor sit Lorem ipsum dolor sit Lorem ipsum dolor sit</p></div>
  <div class="card" style="left:134px;"><h3 style="background:var(--red-dark);">TITLE HERE</h3><p>Lorem ipsum dolor sit Lorem ipsum dolor sit Lorem ipsum dolor sit Lorem ipsum dolor sit Lorem ipsum dolor sit Lorem ipsum dolor sit Lorem ipsum dolor sit Lorem ipsum dolor sit Lorem ipsum dolor sit Lorem ipsum dolor sit Lorem ipsum dolor sit</p></div>
  <div class="card grey" style="left:252px;"><h3 style="background:#555;">TITLE HERE</h3><p>Lorem ipsum dolor sit Lorem ipsum dolor sit Lorem ipsum dolor sit Lorem ipsum dolor sit Lorem ipsum dolor sit Lorem ipsum dolor sit Lorem ipsum dolor sit Lorem ipsum dolor sit Lorem ipsum dolor sit Lorem ipsum dolor sit Lorem ipsum dolor sit</p></div>
  <footer class="footer"><span>Copyright text here</span><span class="page">1</span></footer>
</section>

<!-- Text with image placeholders -->
<section class="slide c3 r2">
  <header class="header"><h2>Project Title Here</h2><div class="brand"><span class="dot"></span>Brass Lantern Guild</div></header>
  <div class="abs" style="left:10px;top:51px;width:175px;">
    <div class="red-head" style="margin-left:3px;">Lorem ipsum dolor sit Lorem</div>
    <p class="copy">Lorem ipsum dolor sit Lorem ipsum dolor sit Lorem ipsum dolor sit Lorem ipsum dolor sit Lorem ipsum dolor sit Lorem ipsum dolor sit Lorem ipsum dolor sit Lorem ipsum dolor sit Lorem ipsum dolor sit Lorem ipsum dolor sit Lorem ipsum dolor sit Lorem ipsum dolor sit Lorem ipsum dolor sit Lorem ipsum dolor sit Lorem ipsum dolor sit Lorem ipsum dolor sit</p>
    <p class="copy" style="margin-top:14px;">Lorem ipsum dolor sit Lorem ipsum dolor sit Lorem ipsum dolor sit Lorem ipsum dolor sit Lorem ipsum dolor sit Lorem ipsum dolor sit Lorem ipsum dolor sit Lorem ipsum dolor sit Lorem ipsum dolor sit Lorem ipsum dolor sit Lorem ipsum dolor sit Lorem ipsum dolor sit Lorem ipsum dolor sit Lorem ipsum dolor sit Lorem ipsum dolor sit Lorem ipsum dolor sit</p>
  </div>
  <div class="abs" role="img" aria-label="Image placeholder" style="left:208px;top:57px;width:149px;height:73px;background:var(--grey-light);"></div>
  <div class="abs" role="img" aria-label="Image placeholder" style="left:208px;top:160px;width:149px;height:73px;background:var(--grey-light);"></div>
  <footer class="footer"><span>Copyright text here</span><span class="page">1</span></footer>
</section>

<!-- Bar chart -->
<section class="slide c1 r3">
  <header class="header"><h2>Project Title Here</h2><div class="brand"><span class="dot"></span>Brass Lantern Guild</div></header>
  <div class="abs" style="left:20px;top:30px;width:340px;">
    <p class="lead">Lorem ipsum dolor sit Lorem ipsum dolor sit &nbsp;Lorem ipsum dolor sit</p>
    <p style="font-size:5.6px;line-height:9.2px;color:#555;margin-top:5px;">Lorem ipsum dolor sit Lorem ipsum dolor sit Lorem ipsum dolor sit Lorem ipsum dolor sit Lorem ipsum dolor sit Lorem ipsum dolor sit Lorem ipsum dolor sit Lorem ipsum dolor sit Lorem ipsum dolor sit Lorem ipsum dolor sit Lorem ipsum dolor sit Lorem ipsum dolor sit Lorem ipsum dolor sit Lorem ipsum dolor sit Lorem ipsum dolor sit</p>
  </div>
  <svg class="abs" style="left:0;top:0" width="371" height="278" font-family="Open Sans, sans-serif" font-size="5.6" fill="#555">
    <text x="21" y="112">Lorem ipsum dolor sit</text>
    <text x="21" y="128">Lorem ipsum dolor sit</text>
    <text x="21" y="145">Lorem ipsum dolor sit</text>
    <text x="21" y="162">Lorem ipsum dolor sit</text>
    <text x="21" y="179">Lorem ipsum dolor sit</text>
    <text x="21" y="197">Lorem ipsum dolor sit</text>
    <text x="21" y="239">Lorem ipsum dolor sit</text>
    <rect x="81" y="195" width="15" height="43" fill="#e06a6a"/>
    <rect x="99" y="161" width="18" height="77" fill="#666"/>
    <rect x="122" y="175" width="18" height="63" fill="#a01a20"/>
    <rect x="144" y="200" width="18" height="38" fill="#666"/>
    <rect x="167" y="227" width="19" height="11" fill="#ec1f27"/>
    <rect x="191" y="234" width="21" height="4" fill="#888"/>
    <rect x="216" y="118" width="18" height="120" fill="#a01a20"/>
    <rect x="239" y="227" width="19" height="11" fill="#666"/>
    <rect x="262" y="233" width="19" height="5" fill="#999"/>
    <rect x="285" y="234" width="22" height="4" fill="#999"/>
  </svg>
  <footer class="footer"><span>Copyright text here</span><span class="page">1</span></footer>
</section>

<!-- Circular diagram -->
<section class="slide c2 r3">
  <header class="header"><h2>Project Title Here</h2><div class="brand"><span class="dot"></span>Brass Lantern Guild</div></header>
  <div class="abs" style="left:298px;top:30px;width:52px;height:230px;background:#f3f4f8;"></div>
  <svg class="abs" style="left:0;top:0" width="371" height="278">
    <g fill="none" stroke-width="11" transform="rotate(-112 188 138)">
      <circle cx="188" cy="138" r="68" stroke="#8b1a20" stroke-dasharray="48 379" stroke-dashoffset="0"/>
      <circle cx="188" cy="138" r="68" stroke="#c8171e" stroke-dasharray="48 379" stroke-dashoffset="-61"/>
      <circle cx="188" cy="138" r="68" stroke="#e0262d" stroke-dasharray="48 379" stroke-dashoffset="-122"/>
      <circle cx="188" cy="138" r="68" stroke="#8fa3a3" stroke-dasharray="48 379" stroke-dashoffset="-183"/>
      <circle cx="188" cy="138" r="68" stroke="#3a3a3a" stroke-dasharray="48 379" stroke-dashoffset="-244"/>
      <circle cx="188" cy="138" r="68" stroke="#4a4e63" stroke-dasharray="48 379" stroke-dashoffset="-305"/>
      <circle cx="188" cy="138" r="68" stroke="#151515" stroke-dasharray="48 379" stroke-dashoffset="-366"/>
    </g>
    <circle cx="188" cy="138" r="15" fill="#ec1f27" stroke="#111" stroke-width="2"/>
    <g fill="none" stroke="#333" stroke-width="0.8">
      <polyline points="62,66 100,66 127,82"/>
      <polyline points="62,148 98,148 120,160"/>
      <polyline points="62,220 110,220 132,202"/>
      <polyline points="318,56 272,56 252,70"/>
      <polyline points="318,131 285,131 262,128"/>
      <polyline points="318,210 278,210 262,196"/>
    </g>
    <g font-family="Open Sans, sans-serif">
      <g font-size="6.8" font-weight="600" fill="#c8171e">
        <text x="18" y="64">Heading Here</text>
        <text x="18" y="146">Heading Here</text>
      </g>
      <text x="18" y="218" font-size="6.8" font-weight="600" fill="#444">Heading Here</text>
      <g font-size="5.2" fill="#555">
        <text x="18" y="73">Subtext here Subtext here Sub-</text><text x="18" y="81">text here Subtext here Subtext</text><text x="18" y="89">here Subtext here</text>
        <text x="18" y="155">Subtext here Subtext here Sub-</text><text x="18" y="163">text here Subtext here Subtext</text><text x="18" y="171">here Subtext here</text>
        <text x="18" y="227">Subtext here Subtext</text><text x="18" y="235">here Subtext here Sub-</text><text x="18" y="243">text here Subtext here</text><text x="18" y="251">Subtext here</text>
      </g>
      <g font-size="6.8" font-weight="600" fill="#444" text-anchor="end">
        <text x="349" y="53">Heading Here</text>
        <text x="349" y="128">Heading Here</text>
        <text x="349" y="208">Heading Here</text>
      </g>
      <g font-size="5.2" fill="#555" text-anchor="end">
        <text x="349" y="62">Subtext here Subtext here Sub-</text><text x="349" y="70">text here Subtext here Subtext</text><text x="349" y="78">here Subtext here</text>
        <text x="349" y="137">Subtext here Subtext here Sub-</text><text x="349" y="145">text here Subtext here Subtext</text><text x="349" y="153">here Subtext here</text>
        <text x="349" y="217">Subtext here Subtext here Sub-</text><text x="349" y="225">text here Subtext here Subtext</text><text x="349" y="233">here Subtext here</text>
      </g>
    </g>
  </svg>
  <footer class="footer"><span>Copyright text here</span><span class="page">1</span></footer>
</section>

<!-- Table -->
<section class="slide c3 r3">
  <header class="header"><h2>Project Title Here</h2><div class="brand"><span class="dot"></span>Brass Lantern Guild</div></header>
  <div class="abs" style="left:20px;top:45px;width:340px;">
    <div class="red-head" style="font-size:7px;">Table Head Here</div>
    <p style="font-size:5px;line-height:7px;color:#aaa;">Lorem ipsum dolor sit Lorem ipsum dolor sit &nbsp;Lorem ipsum dolor sit Lorem ipsum dolor sit &nbsp;Lorem ipsum dolor sit Lorem ipsum dolor Lorem ipsum dolor sit Lorem ipsum dolor sit &nbsp;Lorem ipsum dolor sit Lorem ipsum dolor sit &nbsp;Lorem ipsum dolor sit Lorem ipsum dolor Lorem ipsum dolor sit Lorem ipsum dolor sit &nbsp;Lorem ipsum dolor sit Lorem ipsum dolor sit</p>
  </div>
  <table class="data-table">
    <thead><tr><th>TABLE HEAD HERE</th><th>TABLE HEAD HERE</th><th>TABLE HEAD HERE</th></tr></thead>
    <tbody>
      <tr><td>Subtext here Subtext here</td><td>Subtext here Subtext here</td><td>Subtext here Subtext here</td></tr>
      <tr><td>Subtext here Subtext here</td><td>Subtext here Subtext here</td><td>Subtext here Subtext here</td></tr>
      <tr><td>Subtext here Subtext here</td><td>Subtext here Subtext here</td><td>Subtext here Subtext here</td></tr>
      <tr><td>Subtext here Subtext here</td><td>Subtext here Subtext here</td><td>Subtext here Subtext here</td></tr>
      <tr><td>Subtext here Subtext here</td><td>Subtext here Subtext here</td><td>Subtext here Subtext here</td></tr>
      <tr><td>Subtext here Subtext here</td><td>Subtext here Subtext here</td><td>Subtext here Subtext here</td></tr>
    </tbody>
  </table>
  <footer class="footer"><span>Copyright text here</span><span class="page">1</span></footer>
</section>

<!-- Icon list -->
<section class="slide c1 r4" style="height:278px;">
  <header class="header"><h2>Project Title Here</h2><div class="brand"><span class="dot"></span>Brass Lantern Guild</div></header>
  <div class="icon-row" style="top:48px;">
    <div class="chev"><svg width="22" height="22" viewBox="0 0 22 22" fill="none" stroke="#fff" stroke-width="1.4"><path d="M11 2a6 6 0 0 0-4 10.5c1 1 1 2 1 3h6c0-1 0-2 1-3A6 6 0 0 0 11 2z"/><path d="M8.5 18h5M9 20.5h4"/></svg></div>
    <div class="icon-text"><h4>TEXT HEADING <span>HERE</span></h4><p>Lorem ipsum dolor sit Lorem ipsum dolor sit Lorem ipsum dolor sit Lorem ipsum dolor sit Lorem ipsum dolor sit Lorem ipsum dolor sit Lorem ipsum dolor sit Lorem ipsum dolor sit Lorem ipsum dolor sit Lorem ipsum dolor sit Lorem ipsum dolor sit Lorem ipsum dolor sit Lorem ipsum dolor sit</p></div>
  </div>
  <div class="icon-row" style="top:98px;">
    <div class="chev"><svg width="22" height="22" viewBox="0 0 22 22" fill="#fff"><path d="M11 2l3 7h7l-5.5 4.5 2 7L11 16l-6.5 4.5 2-7L1 9h7z"/></svg></div>
    <div class="icon-text"><h4>TEXT HEADING <span>HERE</span></h4><p>Lorem ipsum dolor sit Lorem ipsum dolor sit Lorem ipsum dolor sit Lorem ipsum dolor sit Lorem ipsum dolor sit Lorem ipsum dolor sit Lorem ipsum dolor sit Lorem ipsum dolor sit Lorem ipsum dolor sit Lorem ipsum dolor sit Lorem ipsum dolor sit Lorem ipsum dolor sit Lorem ipsum dolor sit</p></div>
  </div>
  <div class="icon-row" style="top:148px;">
    <div class="chev"><svg width="22" height="22" viewBox="0 0 22 22" fill="none" stroke="#fff" stroke-width="2.4"><circle cx="11" cy="11" r="8.5"/><path d="M5 5l12 12"/></svg></div>
    <div class="icon-text"><h4>TEXT HEADING <span>HERE</span></h4><p>Lorem ipsum dolor sit Lorem ipsum dolor sit Lorem ipsum dolor sit Lorem ipsum dolor sit Lorem ipsum dolor sit Lorem ipsum dolor sit Lorem ipsum dolor sit Lorem ipsum dolor sit Lorem ipsum dolor sit Lorem ipsum dolor sit Lorem ipsum dolor sit Lorem ipsum dolor sit Lorem ipsum dolor sit</p></div>
  </div>
  <div class="icon-row" style="top:197px;">
    <div class="chev"><svg width="22" height="22" viewBox="0 0 22 22" fill="none" stroke="#fff" stroke-width="1.4"><circle cx="11" cy="11" r="6.5"/><path d="M11 1v7M11 14v7M1 11h7M14 11h7"/><circle cx="11" cy="11" r="1.5" fill="#fff"/></svg></div>
    <div class="icon-text"><h4>TEXT HEADING <span>HERE</span></h4><p>Lorem ipsum dolor sit Lorem ipsum dolor sit Lorem ipsum dolor sit Lorem ipsum dolor sit Lorem ipsum dolor sit Lorem ipsum dolor sit Lorem ipsum dolor sit Lorem ipsum dolor sit Lorem ipsum dolor sit Lorem ipsum dolor sit Lorem ipsum dolor sit Lorem ipsum dolor sit Lorem ipsum dolor sit</p></div>
  </div>
  <footer class="footer"><span>Copyright text here</span><span class="page">1</span></footer>
</section>

<!-- Closing -->
<section class="slide c2 r4 closing">
  <div class="closing-title">Project Title Here</div>
  <div class="contact-box">
    <div class="mark"></div>
    <div class="wordmark" style="font-size:16px;margin-bottom:6px;">Brass Lantern Guild</div>
    <p>COntact Details here &nbsp;COntact Details here<br>COntact Details here &nbsp;COntact Details here<br>COntact Details here</p>
  </div>
  <div class="band-bottom"></div>
</section>

</body>
</html>
```